New business card/stationary for a consulting company

I am looking for a clean and very professional looking business card for my consulting company as well as corresponding stationary. I am uploading our logo. I like simple and powerful for the feel. No graphics but I am open on everything else. Below is my contact information but would like the final to be in a version I can add my employees information into and print. Thank you.

Daniel Whitcombe
dan@ferncliffadvisory.com
2870 North 9th Avenue, Summit Floor, Elm Ridge, Illinois 60531
www.ferncliffadvisory.com

Industry/Entity Type

Consulting

Contact Information for Business Card

Daniel Whitcombe
dan@ferncliffadvisory.com
www.ferncliffadvisory.com

Font styles to use
Serif
Sans Serif

Requirements
Must have
• Our logo and the business card details.
Nice to have
• our website www.ferncliffadvisory.com

```html
<!DOCTYPE html>
<html lang="en">
<head>
<meta charset="utf-8">
<title>Ferncliff Advisory – Business Card</title>
<link rel="stylesheet" href="https://fonts.googleapis.com/css2?family=Montserrat:wght@300;400;600;700&display=swap">
<style>
  :root {
    --brand-blue: #1a0fb0;
    --navy: #12107a;
    --paper: #ffffff;
    --backdrop: #eceef0;
    --ink: #2a2a33;
    --rule: rgba(255,255,255,0.85);
    --photo-light: #e4e4e6;
    --photo-dark: #4a4c55;
  }
  * { box-sizing: border-box; margin: 0; padding: 0; }
  html, body { width: 1200px; height: 900px; overflow: hidden; }
  body {
    background: var(--backdrop);
    font-family: "Montserrat", sans-serif;
    position: relative;
  }
  .card {
    position: absolute;
    left: 340px;
    width: 520px;
    height: 300px;
    box-shadow: 0 6px 18px rgba(0,0,0,0.12);
  }
  /* Back of card */
  .card-back {
    top: 110px;
    background: var(--brand-blue);
    color: #fff;
  }
  .card-back .brand {
    position: absolute;
    left: 0; right: 0; top: 96px;
    display: flex;
    align-items: center;
    justify-content: center;
    gap: 14px;
  }
  .card-back .brand-mark {
    width: 26px; height: 26px;
    background: #fff;
  }
  .card-back .brand-name {
    font-size: 27px;
    font-weight: 400;
    letter-spacing: 2px;
    text-transform: uppercase;
  }
  .card-back .divider {
    position: absolute;
    left: 60px; right: 60px; top: 168px;
    height: 1px;
    background: var(--rule);
  }
  .card-back .address {
    position: absolute;
    left: 0; right: 0; top: 186px;
    text-align: center;
    font-size: 11px;
    font-weight: 600;
    letter-spacing: 0.2px;
  }
  /* Front of card */
  .card-front {
    top: 470px;
    background: var(--paper);
    overflow: hidden;
  }
  .card-front .brand {
    position: absolute;
    left: 40px; top: 52px;
    display: flex;
    align-items: center;
    gap: 10px;
    color: var(--navy);
  }
  .card-front .brand-mark {
    width: 18px; height: 18px;
    background: var(--navy);
  }
  .card-front .brand-name {
    font-size: 17px;
    font-weight: 400;
    letter-spacing: 1px;
    text-transform: uppercase;
  }
  .card-front .person {
    position: absolute;
    left: 58px; top: 112px;
    color: var(--navy);
  }
  .person-name { font-size: 17px; font-weight: 700; }
  .person-role { font-size: 11px; font-weight: 600; margin-top: 4px; }
  .contact-list {
    position: absolute;
    left: 66px; top: 178px;
    list-style: none;
    font-size: 11px;
    color: var(--ink);
  }
  .contact-list li {
    display: flex;
    align-items: center;
    gap: 9px;
    height: 21px;
  }
  .contact-list svg { width: 10px; height: 10px; fill: var(--navy); flex: none; }
  .portrait {
    position: absolute;
    right: 0; top: 20px;
    width: 210px; height: 280px;
    background: linear-gradient(180deg, var(--photo-light) 0%, var(--photo-light) 30%, var(--photo-dark) 75%, #2d2e35 100%);
    border-radius: 90px 90px 0 0;
  }
</style>
</head>
<body>
  <section class="card card-back">
    <div class="brand">
      <span class="brand-mark"></span>
      <span class="brand-name">Ferncliff Advisory</span>
    </div>
    <div class="divider"></div>
    <p class="address">2870 North 9th Avenue, Summit Floor, Elm Ridge, Illinois 60531</p>
  </section>

  <section class="card card-front">
    <div class="brand">
      <span class="brand-mark"></span>
      <span class="brand-name">Ferncliff Advisory</span>
    </div>
    <div class="person">
      <p class="person-name">Daniel Whitcombe</p>
      <p class="person-role">Founder / Principal</p>
    </div>
    <ul class="contact-list">
      <li>
        <svg viewBox="0 0 10 10" aria-hidden="true"><path d="M2 0.5 L3.6 0.5 L4.2 2.8 L3 3.6 C3.6 5 5 6.4 6.4 7 L7.2 5.8 L9.5 6.4 L9.5 8 C9.5 9 8.8 9.5 8 9.5 C4 9.2 0.8 6 0.5 2 C0.5 1.2 1 0.5 2 0.5 Z"/></svg>
        (555) 010 24680
      </li>
      <li>
        <svg viewBox="0 0 10 10" aria-hidden="true"><path d="M2.5 0 H7.5 A1 1 0 0 1 8.5 1 V9 A1 1 0 0 1 7.5 10 H2.5 A1 1 0 0 1 1.5 9 V1 A1 1 0 0 1 2.5 0 Z M3 1.5 V7.5 H7 V1.5 Z"/></svg>
        +15550137264
      </li>
      <li>
        <svg viewBox="0 0 10 10" aria-hidden="true"><path d="M0 2 H10 V8.5 H0 Z M0.6 2.4 L5 5.6 L9.4 2.4 L9.4 3.2 L5 6.4 L0.6 3.2 Z" fill-rule="evenodd"/></svg>
        dan@ferncliffadvisory.com
      </li>
      <li>
        <svg viewBox="0 0 10 10" aria-hidden="true"><circle cx="5" cy="5" r="4.5"/><path d="M0.5 5 H9.5 M5 0.5 V9.5" stroke="#fff" stroke-width="0.8"/></svg>
        www.ferncliffadvisory.com
      </li>
    </ul>
    <div class="portrait" role="img" aria-label="Portrait photo of the card holder in a dark suit and blue tie"></div>
  </section>
</body>
</html>
```